Business Card Design

Electronic Security
Alarm Systems
CCTV
Electronic Access Control
Security System Integration

Industry/Entity Type

Business

Contact Information for Business Card

Gareth Linwood
PO Box 862
Ashgrove Qld 4071
Phone 07 38526147
Mob 0427395816

```html
<!DOCTYPE html>
<html lang="en">
<head>
<meta charset="utf-8">
<title>Norvale Business Card</title>
<link rel="stylesheet" href="https://fonts.googleapis.com/css2?family=Arimo:wght@400;700&display=swap">
<style>
  :root {
    --bg: #e9e6e1;
    --card: #ffffff;
    --ink: #1d1d1d;
    --accent: #f06a2c;
    --rule: #111111;
  }
  * { margin: 0; padding: 0; box-sizing: border-box; }
  html, body { width: 1200px; height: 800px; overflow: hidden; }
  body {
    background: var(--bg);
    font-family: "Arimo", Arial, sans-serif;
    color: var(--ink);
    position: relative;
  }
  .card {
    position: absolute;
    left: 100px; top: 114px;
    width: 1000px; height: 572px;
    background: var(--card);
    box-shadow: 0 6px 24px rgba(0,0,0,0.12);
  }
  .brand {
    position: absolute;
    left: 70px; top: 250px;
    display: flex; align-items: center; gap: 16px;
  }
  .brand-mark {
    width: 40px; height: 40px;
    background: var(--accent);
  }
  .brand-name {
    font-size: 50px; font-weight: 400; letter-spacing: 2px;
    color: var(--ink);
  }
  .divider {
    position: absolute;
    left: 430px; top: 70px;
    width: 2px; height: 430px;
    background: var(--rule);
  }
  .person {
    position: absolute;
    right: 70px; top: 64px;
    font-size: 44px; font-weight: 700;
    color: var(--accent);
    word-spacing: 14px;
  }
  .contacts {
    position: absolute;
    left: 490px; top: 150px;
    list-style: none;
    font-size: 22px;
  }
  .contacts li {
    display: flex; align-items: center; gap: 16px;
    height: 38px;
  }
  .contacts svg { width: 22px; height: 22px; fill: var(--accent); flex: none; }
  .services-title {
    position: absolute;
    left: 490px; top: 290px;
    font-size: 22px;
  }
  .services {
    position: absolute;
    left: 490px; top: 330px;
    list-style: none;
    font-size: 22px;
  }
  .services li {
    display: flex; align-items: center; gap: 20px;
    height: 34px;
  }
  .services svg { width: 18px; height: 18px; stroke: var(--accent); stroke-width: 2; flex: none; }
</style>
</head>
<body>
  <div class="card">
    <div class="brand">
      <span class="brand-mark"></span>
      <span class="brand-name">NORVALE</span>
    </div>

    <div class="divider"></div>

    <h1 class="person">Gareth Linwood</h1>

    <ul class="contacts">
      <li>
        <svg viewBox="0 0 24 24"><path d="M6.6 10.8a15 15 0 0 0 6.6 6.6l2.2-2.2c.3-.3.7-.4 1-.2 1.1.4 2.3.6 3.6.6.6 0 1 .4 1 1V20c0 .6-.4 1-1 1A17 17 0 0 1 3 4c0-.6.4-1 1-1h3.5c.6 0 1 .4 1 1 0 1.3.2 2.5.6 3.6.1.3 0 .7-.2 1z"/></svg>
        <span>07 38526147</span>
      </li>
      <li>
        <svg viewBox="0 0 24 24"><path d="M7 1h10a2 2 0 0 1 2 2v18a2 2 0 0 1-2 2H7a2 2 0 0 1-2-2V3a2 2 0 0 1 2-2zm0 3v14h10V4zm5 15.5a1.2 1.2 0 1 0 0 2.4 1.2 1.2 0 0 0 0-2.4z"/></svg>
        <span>0427395816</span>
      </li>
      <li>
        <svg viewBox="0 0 24 24"><path d="M12 2a7 7 0 0 0-7 7c0 5.2 7 13 7 13s7-7.8 7-13a7 7 0 0 0-7-7zm0 9.5a2.5 2.5 0 1 1 0-5 2.5 2.5 0 0 1 0 5z"/></svg>
        <span>PO Box 862 Ashgrove Qld 4071</span>
      </li>
    </ul>

    <p class="services-title">Service</p>

    <ul class="services">
      <li><svg viewBox="0 0 20 20"><path d="M10 2v16M2 10h16M4.3 4.3l11.4 11.4M15.7 4.3L4.3 15.7"/></svg><span>Electronic Security</span></li>
      <li><svg viewBox="0 0 20 20"><path d="M10 2v16M2 10h16M4.3 4.3l11.4 11.4M15.7 4.3L4.3 15.7"/></svg><span>Alarm Systems</span></li>
      <li><svg viewBox="0 0 20 20"><path d="M10 2v16M2 10h16M4.3 4.3l11.4 11.4M15.7 4.3L4.3 15.7"/></svg><span>CCTV</span></li>
      <li><svg viewBox="0 0 20 20"><path d="M10 2v16M2 10h16M4.3 4.3l11.4 11.4M15.7 4.3L4.3 15.7"/></svg><span>Electronic Access Control</span></li>
      <li><svg viewBox="0 0 20 20"><path d="M10 2v16M2 10h16M4.3 4.3l11.4 11.4M15.7 4.3L4.3 15.7"/></svg><span>Security System Integration</span></li>
    </ul>
  </div>
</body>
</html>
```